Organization and people consulting firm needs a website design

I need a website that promotes and explains the consulting service we will provide. The organization is called Bluefinch Advisory Partners. Our services include organization design, employee experience, change management, and executive coaching. I would like to see a simple clean and professional design, that reflects a modern and forward looking professional services company

Target Market(s)

Mid market and large companies

Industry/Entity Type

Management Consulting

Coding

Coded - Design and coding required

Number of Pages Required

5+ page

Font styles to use
Sans Serif

Colors

Designer to choose colors to be used in the design.

Requirements
Must have
• The following pages: Home, The Way We Work, What We Do, Our Founder, Insights, Contact.
• Search button.
• Hyper links (will be provided with main body text)
• Scrolling website with summaries at top level and links to more detail at lower level (like this website: veltracore.com)
• Company logo (uploaded)
• I have text for each of the pages that I can upload once the basic design is done
Should not have
• No clutter, keep the design clean

```html
<!DOCTYPE html>
<html lang="en">
<head>
<meta charset="utf-8">
<title>Bluefinch Advisory Partners</title>
<link href="https://fonts.googleapis.com/css2?family=Lora:wght@400;700&family=Roboto:wght@400;500;700&display=swap" rel="stylesheet">
<style>
:root{
  --red:#d9102f;
  --dark:#2b2b2b;
  --black:#111111;
  --text:#333333;
  --muted:#7a7a7a;
  --light:#f1f1f1;
  --white:#ffffff;
  --green:#4caf50;
}
*{margin:0;padding:0;box-sizing:border-box}
html,body{width:1200px;height:2927px;overflow:hidden}
body{position:relative;font-family:'Roboto',sans-serif;color:var(--text);background:var(--white)}
.abs{position:absolute}
.serif{font-family:'Lora',serif}
.topbar{left:0;top:0;width:1200px;height:39px;background:var(--dark);color:#ddd;font-size:14px}
.topbar .contact{left:98px;top:11px;display:flex;gap:28px;align-items:center}
.topbar .contact span{display:flex;align-items:center;gap:8px}
.search{left:874px;top:0;width:225px;height:39px;background:var(--red);color:#fff;font-size:14px;padding:11px 14px}
.search svg{position:absolute;right:14px;top:12px}
.header{left:0;top:39px;width:1200px;height:109px;background:#fff}
.logo{left:98px;top:36px;display:flex;align-items:center;gap:12px}
.logo .mark{width:30px;height:30px;background:var(--red)}
.logo .name{font-family:'Lora',serif;font-weight:700;font-size:30px;color:var(--red);letter-spacing:.5px}
.nav{right:98px;top:48px;display:flex;gap:18px;font-size:14.5px;font-weight:500;color:var(--text)}
.nav .active{color:var(--red)}
.hero{left:0;top:148px;width:1200px;height:556px;background:linear-gradient(100deg,#8c8478 0%,#cfc5b8 35%,#e9e7e4 60%,#f4f4f4 100%)}
.hero-title{left:640px;top:276px;font-family:'Lora',serif;font-weight:700;color:var(--red);font-size:66px;letter-spacing:2px;line-height:1}
.hero-sub{left:640px;top:358px;font-family:'Lora',serif;font-weight:700;color:#222;font-size:37px;letter-spacing:4px}
.hero-text{left:640px;top:428px;width:470px;font-size:16.5px;line-height:27px;color:#222}
.btn-red{left:640px;top:513px;width:170px;height:51px;border-radius:26px;background:var(--red);color:#fff;font-size:16px;font-weight:500;display:flex;align-items:center;justify-content:center;gap:6px}
.arrow-nav{width:34px;height:34px;border-radius:50%;background:rgba(90,90,90,.7);display:flex;align-items:center;justify-content:center}
.down{left:575px;top:680px;width:48px;height:48px;border-radius:50%;background:#fff;box-shadow:0 2px 8px rgba(0,0,0,.15);display:flex;align-items:center;justify-content:center;z-index:2}
.section-title{left:0;width:1200px;text-align:center;font-family:'Lora',serif;font-weight:700;font-size:30px;color:#111}
.ghost{left:0;width:1200px;text-align:center;font-family:'Lora',serif;font-weight:700;font-size:54px;color:rgba(0,0,0,.06);letter-spacing:1px}
.para{left:0;width:1200px;text-align:center;font-size:13px;line-height:27px;color:#555}
.btn-outline{height:43px;border:1.5px solid #bbb;border-radius:22px;background:#fff;color:var(--red);font-size:14px;font-weight:500;display:flex;align-items:center;justify-content:center;gap:6px}
.way{left:0;top:704px;width:1200px;height:428px;background:linear-gradient(180deg,#fafafa,#f3f3f3)}
.what{left:0;top:1132px;width:1200px;height:453px;background:linear-gradient(180deg,#ececec,#f7f7f7)}
.service{width:240px;text-align:center}
.service h3{font-size:20px;font-weight:400;color:#222;margin-top:14px}
.service p{font-size:12px;line-height:24px;color:#777;margin-top:8px}
.founder{left:0;top:1585px;width:1200px;height:483px;background:#fff}
.vertical{left:28px;top:1700px;writing-mode:vertical-rl;transform:rotate(180deg);font-family:'Lora',serif;font-weight:700;font-size:48px;color:rgba(217,16,47,.12);letter-spacing:4px}
.founder-photo{left:100px;top:1678px;width:286px;height:294px;background:linear-gradient(160deg,#d8d8d8,#8a8a8a 60%,#3c3c3c);box-shadow:0 0 0 1px #e4e4e4}
.name-tag{left:100px;top:1877px;width:212px;height:45px;background:var(--red);color:#fff;font-family:'Lora',serif;font-weight:700;font-size:19px;padding:10px 14px}
.founder h2{left:437px;top:1672px;font-family:'Lora',serif;font-weight:700;font-size:30px;color:#111}
.founder .lead{left:437px;top:1722px;font-family:'Lora',serif;font-size:17px;color:var(--red)}
.founder .body{left:437px;top:1770px;width:665px;font-size:13px;line-height:23px;color:#666}
.insights{left:0;top:2068px;width:1200px;height:542px;background:linear-gradient(180deg,#fbfbfb,#efefef)}
.card{width:480px;height:215px;background:#fff;box-shadow:0 1px 4px rgba(0,0,0,.08)}
.card .img{position:absolute;left:0;top:0;width:191px;height:215px}
.card .content{position:absolute;left:216px;top:22px;width:250px}
.card h3{font-size:17px;font-weight:700;color:#111}
.card .date{font-size:12.5px;color:var(--green);margin-top:8px;display:flex;align-items:center;gap:6px}
.card p{font-size:12.5px;line-height:24px;color:#666;margin-top:10px}
.card .meta{display:flex;justify-content:space-between;margin-top:12px;font-size:13px;color:#777}
.card .meta b{color:var(--red);font-weight:500}
.footer{left:0;top:2610px;width:1200px;height:317px;background:var(--black);color:#fff}
.footer h4{font-size:16px;font-weight:500;letter-spacing:.3px}
.footer ul{list-style:none;margin-top:22px}
.footer li{font-size:13px;line-height:22.5px;color:#ddd}
.footer li::before{content:"» ";}
.news p{font-size:12.5px;color:#ddd;margin-top:20px}
.field{left:695px;top:2755px;width:404px;height:49px;border-radius:25px;background:#fff;font-size:14px;color:#888;padding:15px 25px}
.subscribe{left:980px;top:2759px;width:115px;height:41px;border-radius:21px;background:var(--red);color:#fff;font-size:14px;font-weight:700;display:flex;align-items:center;justify-content:center}
.social{left:98px;top:2862px;display:flex;gap:20px}
.social span{width:22px;height:22px;border-radius:50%;background:#fff}
.social span.hl{background:var(--red)}
.copy{right:125px;top:2870px;font-size:12.5px;color:#eee}
</style>
</head>
<body>

<div class="abs topbar">
  <div class="abs contact">
    <span><svg width="12" height="12" viewBox="0 0 24 24"><path fill="#ddd" d="M6.6 10.8a15 15 0 0 0 6.6 6.6l2.2-2.2c.3-.3.7-.4 1-.2 1.1.4 2.3.6 3.6.6.6 0 1 .4 1 1V20c0 .6-.4 1-1 1A17 17 0 0 1 3 4c0-.6.4-1 1-1h3.5c.6 0 1 .4 1 1 0 1.3.2 2.5.6 3.6.1.3 0 .7-.2 1z"/></svg>+1-555-014-2290</span>
    <span><svg width="13" height="10" viewBox="0 0 26 20"><rect width="26" height="20" rx="2" fill="#ddd"/><path d="M1 2l12 9 12-9" stroke="#2b2b2b" stroke-width="2" fill="none"/></svg>daniel.hartley@bluefinchadvisory.example</span>
  </div>
  <div class="abs search">Search...
    <svg width="14" height="14" viewBox="0 0 24 24"><circle cx="10" cy="10" r="7" stroke="#fff" stroke-width="3" fill="none"/><path d="M15 15l7 7" stroke="#fff" stroke-width="3"/></svg>
  </div>
</div>

<header class="abs header">
  <div class="abs logo"><span class="mark"></span><span class="name">Bluefinch</span></div>
  <nav class="abs nav">
    <span class="active">HOME</span><span>THE WAY WE WORK</span><span>WHAT WE DO</span><span>OUR FOUNDER</span><span>INSIGHTS</span><span>CONTACT</span>
  </nav>
</header>

<section class="abs hero" role="img" aria-label="Photo of a smiling consultant with a headset at a bright office desk"></section>
<div class="abs arrow-nav" style="left:22px;top:409px"><svg width="10" height="14" viewBox="0 0 10 14"><path d="M8 1L2 7l6 6" stroke="#fff" stroke-width="2" fill="none"/></svg></div>
<div class="abs arrow-nav" style="left:1140px;top:409px"><svg width="10" height="14" viewBox="0 0 10 14"><path d="M2 1l6 6-6 6" stroke="#fff" stroke-width="2" fill="none"/></svg></div>
<div class="abs hero-title">BLUEFINCH</div>
<div class="abs hero-sub">ADVISORY PARTNERS</div>
<div class="abs hero-text">Our services include organisation design, employee experience, change management, and executive coaching.</div>
<div class="abs btn-red">READ MORE <svg width="15" height="15" viewBox="0 0 16 16"><circle cx="8" cy="8" r="8" fill="#fff"/><path d="M5 8h6M8 5l3 3-3 3" stroke="#d9102f" stroke-width="2" fill="none"/></svg></div>
<div class="abs down"><svg width="12" height="20" viewBox="0 0 12 20"><path d="M6 1v17M1 13l5 5 5-5" stroke="#333" stroke-width="2" fill="none"/></svg></div>

<section class="abs way"></section>
<div class="abs ghost" style="top:770px">THE WAY WE WORK</div>
<div class="abs section-title" style="top:788px">THE WAY WE WORK</div>
<p class="abs para" style="top:868px">Nemo enim ipsam voluptatem quia voluptas sit aspernatur aut odit aut fugit, sed quia consequuntur magni dolores eos qui ratione<br>voluptatem sequi nesciunt. Neque porro quisquam est, qui dolorem ipsum quia dolor sit amet, consectetur, adipisci velit, sequia<br>non numquam eius modi tempora incidunt ut labore et dolore magnam aliquam quaerat voluptatem.</p>
<div class="abs btn-outline" style="left:521px;top:993px;width:158px">READ MORE <svg width="14" height="14" viewBox="0 0 16 16"><circle cx="8" cy="8" r="8" fill="#d9102f"/><path d="M5 8h6M8 5l3 3-3 3" stroke="#fff" stroke-width="2" fill="none"/></svg></div>

<section class="abs what"></section>
<div class="abs ghost" style="top:1184px">WHAT WE DO</div>
<div class="abs section-title" style="top:1202px">WHAT WE DO</div>
<p class="abs para" style="top:1259px;line-height:24px">Nemo enim ipsam voluptatem quia voluptas sit aspernatur aut odit aut fugit, sed quia consequun-<br>tur magni dolores eos qui ratione voluptatem sequi nesciunt.</p>

<div class="abs service" style="left:93px;top:1348px">
  <svg width="70" height="60" viewBox="0 0 70 60" fill="none" stroke="#d9102f" stroke-width="2.5"><rect x="25" y="3" width="20" height="13"/><rect x="3" y="24" width="20" height="13"/><rect x="47" y="24" width="20" height="13"/><rect x="3" y="44" width="20" height="13"/><rect x="25" y="44" width="20" height="13"/><rect x="47" y="44" width="20" height="13"/><path d="M35 16v28M13 20h44M13 20v4M57 20v4"/></svg>
  <h3>Organisation Design</h3><p>Nemo enim ipsam voluptatem quia voluptas<br>sit aspernatur aut odit aut fugit</p>
</div>
<div class="abs service" style="left:352px;top:1348px">
  <svg width="80" height="60" viewBox="0 0 80 60" fill="none" stroke="#d9102f" stroke-width="2.5"><circle cx="40" cy="16" r="9"/><path d="M24 50c0-12 7-19 16-19s16 7 16 19z"/><circle cx="16" cy="22" r="7"/><path d="M3 52c0-10 6-15 13-15 4 0 7 1 9 4"/><circle cx="64" cy="22" r="7"/><path d="M77 52c0-10-6-15-13-15-4 0-7 1-9 4"/></svg>
  <h3>Employee Experience</h3><p>Nemo enim ipsam voluptatem quia voluptas<br>sit aspernatur aut odit aut fugit</p>
</div>
<div class="abs service" style="left:608px;top:1348px">
  <svg width="70" height="60" viewBox="0 0 70 60" fill="none" stroke="#d9102f" stroke-width="2.5"><circle cx="35" cy="22" r="7"/><path d="M22 52c0-11 6-17 13-17s13 6 13 17"/><path d="M14 18a24 24 0 0 1 36-12M56 42a24 24 0 0 1-36 12"/><path d="M50 1l1 6-6 1M20 59l-1-6 6-1"/></svg>
  <h3>Change Management</h3><p>Nemo enim ipsam voluptatem quia voluptas<br>sit aspernatur aut odit aut fugit</p>
</div>
<div class="abs service" style="left:867px;top:1348px">
  <svg width="80" height="60" viewBox="0 0 80 60" fill="none" stroke="#d9102f" stroke-width="2.5"><path d="M8 26a14 14 0 1 1 26 7l-4 4v10h-12v-7c-6-3-10-8-10-14z"/><path d="M72 26a14 14 0 1 0-26 7l4 4v10h12v-7c6-3 10-8 10-14z"/><circle cx="32" cy="8" r="3"/><circle cx="40" cy="5" r="3"/><circle cx="48" cy="8" r="3"/></svg>
  <h3>Executive Coaching</h3><p>Nemo enim ipsam voluptatem quia voluptas<br>sit aspernatur aut odit aut fugit</p>
</div>

<section class="abs founder"></section>
<div class="abs vertical">DANIEL</div>
<div class="abs founder-photo" role="img" aria-label="Black and white portrait of the founder in a suit and tie"></div>
<div class="abs name-tag">Daniel Hartley</div>
<div class="founder">
  <h2 class="abs" style="left:437px;top:1672px">OUR FOUNDER</h2>
  <div class="abs lead">Daniel Hartley, Why I Became an Bluefinch Advisory.</div>
  <p class="abs body">At vero eos et accusamus et iusto odio dignissimos ducimus qui blanditiis praesentium voluptatum deleniti atque corrupti quos dolores et quas molestias excepturi sint occaecati cupiditate non provident, similique sunt in culpa qui officia deserunt mollitia animi, id est laborum et dolorum fuga. Et harum quidem rerum facilis est et expedita distinctio. Nam libero tempore, cum soluta nobis est eligendi optio cumque nihil impedit quo minus id quod maxime placeat facere possimus omnis voluptas assumenda...</p>
</div>
<div class="abs btn-outline" style="left:437px;top:1928px;width:187px">MORE ABOUT ME <svg width="14" height="14" viewBox="0 0 16 16"><circle cx="8" cy="8" r="8" fill="#d9102f"/><path d="M5 8h6M8 5l3 3-3 3" stroke="#fff" stroke-width="2" fill="none"/></svg></div>

<section class="abs insights"></section>
<div class="abs ghost" style="top:2130px">BLUEFINCH INSIGHTS</div>
<div class="abs section-title" style="top:2140px">BLUEFINCH INSIGHTS</div>

<article class="abs card" style="left:100px;top:2228px">
  <div class="img" role="img" aria-label="Photo of a presenter at a whiteboard addressing a seated group" style="background:linear-gradient(135deg,#e9e9e9,#9aa6b8 60%,#3b4d6e)"></div>
  <div class="content">
    <h3>IPSAM VOLUPTATEM</h3>
    <div class="date"><svg width="12" height="12" viewBox="0 0 12 12"><rect x="0" y="1" width="12" height="11" rx="1" fill="#4caf50"/><rect x="1.5" y="4" width="9" height="6.5" fill="#fff"/></svg>APRIL 02,2018</div>
    <p>At vero eos et accusam muset iusto odio dignissimos ducimus qu praeseum tre voluptatum deleniti atque</p>
    <div class="meta"><b>READ MORE</b><span>35 comments</span></div>
  </div>
</article>
<article class="abs card" style="left:620px;top:2228px">
  <div class="img" role="img" aria-label="Photo of a speaker at a podium in front of an audience" style="background:linear-gradient(135deg,#5a2a1c,#a0603c 50%,#2a1a14)"></div>
  <div class="content">
    <h3>ACCUSAMUS ET IUSTO</h3>
    <div class="date"><svg width="12" height="12" viewBox="0 0 12 12"><rect x="0" y="1" width="12" height="11" rx="1" fill="#4caf50"/><rect x="1.5" y="4" width="9" height="6.5" fill="#fff"/></svg>APRIL 08,2018</div>
    <p>At vero eos et accusam muset iusto odio dignissimos ducimus qu praeseum tre voluptatum deleniti atque</p>
    <div class="meta"><b>READ MORE</b><span>35 comments</span></div>
  </div>
</article>
<div class="abs btn-outline" style="left:501px;top:2488px;width:199px">VIEW ALL INSIGHTS <svg width="14" height="14" viewBox="0 0 16 16"><circle cx="8" cy="8" r="8" fill="#d9102f"/><path d="M5 8h6M8 5l3 3-3 3" stroke="#fff" stroke-width="2" fill="none"/></svg></div>

<footer class="abs footer">
  <div class="abs" style="left:98px;top:57px">
    <h4>QUICK LINKS</h4>
    <ul><li>The Way We Work</li><li>What We Do</li><li>Our Founder</li><li>Insights</li><li>Contact</li></ul>
  </div>
  <div class="abs" style="left:297px;top:57px">
    <h4>SERVICES</h4>
    <ul><li>Organisation Design</li><li>Employee Experience</li><li>Change Management</li><li>Executive Coaching</li></ul>
  </div>
  <div class="abs news" style="left:693px;top:57px">
    <h4>SUBSCRIBE TO OUR NEWSLETTER</h4>
    <p>Register your Email Address to get a more information about us!</p>
  </div>
</footer>
<div class="abs field">Your Email</div>
<div class="abs subscribe">SUBSCRIBE</div>
<div class="abs social"><span></span><span></span><span class="hl"></span><span></span><span></span></div>
<div class="abs copy">Copyrights © 2018 Bluefinch Advisory Partners. All Rights Reserved.</div>

</body>
</html>
```